Modern Business Card

Modern professional business card with more than just logo and demographic info. Something memorable.

We are a trendy/modern chiropractic group with an emphasis on neurology, hence the minimalist-type brain logo. We want to convey that modern and technical aspect with professionalism and the elite nature of our practice environment.

```html
<!DOCTYPE html>
<html lang="en">
<head>
<meta charset="utf-8">
<title>Cadence Chiropractic – Business Card</title>
<link rel="stylesheet" href="https://fonts.googleapis.com/css2?family=Open+Sans:wght@400;600;800&display=swap">
<style>
  :root {
    --brand-blue: #3f74b3;
    --card-light: #f7f7f7;
    --card-shade: #e2e2e2;
    --ink: #1a1a1a;
    --rule: #222222;
    --stage: #ececec;
  }
  * { box-sizing: border-box; margin: 0; padding: 0; }
  html, body {
    width: 1200px; height: 780px; overflow: hidden;
    background: var(--stage);
    font-family: "Open Sans", Arial, sans-serif;
  }
  .canvas {
    width: 1200px; height: 780px;
    display: flex; align-items: center; justify-content: center; gap: 40px;
  }
  .card {
    position: relative;
    width: 540px; height: 309px;
    border-radius: 14px;
    overflow: hidden;
    background: linear-gradient(170deg, var(--card-shade) 0%, var(--card-light) 70%);
    box-shadow: 0 10px 28px rgba(0,0,0,.18);
  }

  /* Front */
  .front__band {
    position: absolute; left: 0; right: 0; top: 92px; height: 104px;
    background: var(--brand-blue);
    display: flex; align-items: center; justify-content: center; gap: 14px;
  }
  .brand-mark { width: 18px; height: 18px; background: #fff; border-radius: 50%; }
  .brand-name {
    color: #fff; font-weight: 600; font-size: 30px; letter-spacing: 2px; line-height: 1;
  }
  .front__web {
    position: absolute; left: 22px; right: 22px; top: 244px;
    display: flex; align-items: center; gap: 16px;
    color: var(--brand-blue); font-size: 14px; letter-spacing: .5px;
  }
  .front__web .line { flex: 1; height: 1px; background: var(--brand-blue); }

  /* Back */
  .back__strip {
    position: absolute; left: 0; right: 0; bottom: 0; height: 12px;
    background: var(--brand-blue);
  }
  .back__tab {
    position: absolute; left: 0; top: 178px; width: 10px; height: 14px;
    background: var(--brand-blue);
  }
  .person { position: absolute; left: 40px; top: 118px; }
  .person__name { font-size: 28px; color: var(--ink); line-height: 1; letter-spacing: .5px; }
  .person__name strong { font-weight: 800; }
  .person__role { font-size: 13px; color: var(--ink); margin-top: 4px; letter-spacing: .5px; }
  .person__rule {
    position: absolute; left: 56px; top: 186px; width: 180px; height: 3px;
    background: var(--brand-blue);
  }
  .divider {
    position: absolute; left: 236px; top: 186px; width: 280px; height: 1px;
    background: var(--rule);
  }
  .contacts { position: absolute; left: 58px; top: 210px; list-style: none; }
  .contacts li {
    display: flex; align-items: center; gap: 14px;
    font-size: 14px; color: var(--ink); margin-bottom: 12px;
  }
  .icon {
    width: 24px; height: 20px; border-radius: 3px; background: var(--brand-blue);
    display: flex; align-items: center; justify-content: center; flex: none;
  }
  .address {
    position: absolute; right: 36px; top: 74px;
    display: flex; align-items: flex-start; gap: 10px;
    font-size: 13px; color: var(--ink); line-height: 1.35; text-align: right;
  }
</style>
</head>
<body>
<main class="canvas">

  <section class="card card--front" aria-label="Card front">
    <div class="front__band">
      <span class="brand-mark"></span>
      <span class="brand-name">CADENCE CHIROPRACTIC</span>
    </div>
    <div class="front__web">
      <span class="line"></span>
      <span>www.cadencechiro.com</span>
      <span class="line"></span>
    </div>
  </section>

  <section class="card card--back" aria-label="Card back">
    <div class="back__tab"></div>

    <div class="address">
      <p>48 Harlow Street, Suite 3<br>Brookfield, USA, 40112</p>
      <span class="icon">
        <svg width="10" height="12" viewBox="0 0 10 12"><path d="M5 0a4 4 0 0 1 4 4c0 3-4 8-4 8S1 7 1 4a4 4 0 0 1 4-4z" fill="#fff"/><circle cx="5" cy="4" r="1.5" fill="#3f74b3"/></svg>
      </span>
    </div>

    <div class="person">
      <p class="person__name"><strong>DANA</strong> WHITFORD</p>
      <p class="person__role">FOUNDER &amp; CEO</p>
    </div>
    <div class="person__rule"></div>
    <div class="divider"></div>

    <ul class="contacts">
      <li>
        <span class="icon">
          <svg width="8" height="12" viewBox="0 0 8 12"><rect x="0.75" y="0.75" width="6.5" height="10.5" rx="1" fill="none" stroke="#fff" stroke-width="1.5"/></svg>
        </span>
        555-210-4837
      </li>
      <li>
        <span class="icon">
          <svg width="12" height="10" viewBox="0 0 12 10"><path d="M1 4a7 7 0 0 1 10 0M3 6a4 4 0 0 1 6 0" fill="none" stroke="#fff" stroke-width="1.3"/><circle cx="6" cy="8.3" r="1" fill="#fff"/></svg>
        </span>
        www.cadencechiro.com
      </li>
    </ul>

    <div class="back__strip"></div>
  </section>

</main>
</body>
</html>
```